Front page on www.brightmarkgoods.com modern service ads - each ad for each featured service

We need to have initial 5 banners to be created for our soon to be launched new site,. These are 5 rotating banners that will showcase our companies key features. We are looking for a modern stylish yet simple look to highlight these features. Something thats very inviting and modern to fit the look of the new website.

5 banners need to be, information can be found on www.brightmarkgoods.com about these. Please ask if any questions

Why us?
Art Services
Order Process
Current promotions
Clearance products

please also note. the design will be going onto this website. http://new.brightmarkgoods.com/ Please base actual designs , color schemes etc.. for the new site.

Target Market(s)

Small businesses that purchase marketing promotional goods, to promote their business

Industry/Entity Type

Promotional Product

Font styles to use
Sans Serif

Requirements
Must have
• Size of the banner is 965 x 400 px
Nice to have
• Modern elements,, very clean and minimal look
Should not have
• no cheap generic clip art

```html
<!DOCTYPE html>
<html lang="en">
<head>
<meta charset="UTF-8">
<title>Bright Mark Goods – Feature Banners</title>
<link href="https://fonts.googleapis.com/css2?family=Montserrat:wght@400;600;700&display=swap" rel="stylesheet">
<style>
  :root{
    --blue:#2a4d9c;
    --green:#5aa630;
    --white:#ffffff;
    --panel-grey:#f0f0f2;
  }
  *{margin:0;padding:0;box-sizing:border-box}
  html,body{width:805px;height:1200px;overflow:hidden;background:var(--white)}
  body{font-family:'Montserrat',Arial,sans-serif;color:var(--blue);position:relative}
  .banner{position:absolute;left:0;width:805px;overflow:hidden}
  .banner--why{top:0;height:230px}
  .banner--art{top:230px;height:255px}
  .banner--order{top:485px;height:230px;background:var(--panel-grey)}
  .banner--promo{top:715px;height:242px}
  .banner--clear{top:957px;height:243px}
  .photo{
    position:absolute;
    -webkit-mask-image:linear-gradient(90deg,transparent 0,#000 14%,#000 86%,transparent 100%);
            mask-image:linear-gradient(90deg,transparent 0,#000 14%,#000 86%,transparent 100%);
  }
  .photo--why{left:340px;top:0;width:260px;height:230px;
    background:linear-gradient(180deg,#e2c07f 0%,#e9cfa3 22%,#f1d3c4 40%,#f3ece8 58%,#f6f6f8 100%)}
  .photo--art{left:445px;top:49px;width:195px;height:206px;
    background:linear-gradient(180deg,#3a3230 0%,#6b4f40 12%,#d6a98c 28%,#c9dcf0 46%,#a9c9ea 70%,#bcd6ef 100%)}
  .photo--order{left:121px;top:0;width:205px;height:230px;
    background:linear-gradient(180deg,#e8e6e6 0%,#d9bd8e 16%,#e7cfa8 30%,#efcbb4 48%,#f1e4dc 66%,#f4f1ee 100%)}
  .photo--promo{left:478px;top:12px;width:265px;height:230px;
    background:linear-gradient(180deg,#7a4a2c 0%,#8e5a36 22%,#a8734f 38%,#6f84a6 55%,#556f97 72%,#4b628a 100%)}
  .photo--clear{left:100px;top:15px;width:290px;height:228px;
    background:linear-gradient(180deg,#f4f5f7 0%,#ecdcc2 16%,#f0d7c2 38%,#f1d6c8 60%,#f7cfcf 80%,#f8d3d3 100%)}
  .brackets{position:absolute;overflow:visible}
  .brackets path{fill:none;stroke:var(--green);stroke-width:2}
  .headline{position:absolute;font-weight:700;font-size:22px;letter-spacing:-0.8px;line-height:1;white-space:nowrap;transform:translate(-50%,-50%);text-align:center}
  .headline .light{font-weight:400}
  .headline--stack{line-height:27px}
  .learn-more{position:absolute;display:flex;align-items:center;gap:4px;font-weight:600;font-size:9px;letter-spacing:-0.3px;color:var(--blue);text-decoration:none;white-space:nowrap;transform:translateY(-50%)}
  .learn-more svg{width:23px;height:6px}
</style>
</head>
<body>

<section class="banner banner--why">
  <div class="photo photo--why" role="img" aria-label="Smiling blonde woman in a white blouse holding a phone and a banknote"></div>
  <svg class="brackets" style="left:124px;top:79px" width="237" height="72" viewBox="0 0 237 72">
    <path d="M32 1H1V71H32"/><path d="M205 1H236V71H205"/>
  </svg>
  <h2 class="headline" style="left:243px;top:115px">WHY <span class="light">US?</span></h2>
  <a class="learn-more" style="left:199px;top:148px" href="#"><svg viewBox="0 0 23 6"><line x1="0" y1="3" x2="18" y2="3" stroke="#2a4d9c" stroke-width="1"/><path d="M17 0.5L22 3L17 5.5Z" fill="#2a4d9c"/></svg>LEARN MORE</a>
</section>

<section class="banner banner--art">
  <div class="photo photo--art" role="img" aria-label="Smiling man in a light blue shirt pointing to his open palm"></div>
  <svg class="brackets" style="left:189px;top:92px" width="261" height="72" viewBox="0 0 261 72">
    <path d="M32 1H1V71H32"/><path d="M229 1H260V71H229"/>
  </svg>
  <h2 class="headline" style="left:320px;top:128px">ART SERVICES</h2>
  <a class="learn-more" style="left:276px;top:190px" href="#"><svg viewBox="0 0 23 6"><line x1="0" y1="3" x2="18" y2="3" stroke="#2a4d9c" stroke-width="1"/><path d="M17 0.5L22 3L17 5.5Z" fill="#2a4d9c"/></svg>LEARN MORE</a>
</section>

<section class="banner banner--order">
  <div class="photo photo--order" role="img" aria-label="Smiling blonde woman in a cream sweater with hands at her neck"></div>
  <svg class="brackets" style="left:308px;top:79px" width="304" height="72" viewBox="0 0 304 72">
    <path d="M32 1H1V71H32"/><path d="M272 1H303V71H272"/>
  </svg>
  <h2 class="headline" style="left:457px;top:115px">ORDER PROCESS</h2>
  <a class="learn-more" style="left:417px;top:171px" href="#"><svg viewBox="0 0 23 6"><line x1="0" y1="3" x2="18" y2="3" stroke="#2a4d9c" stroke-width="1"/><path d="M17 0.5L22 3L17 5.5Z" fill="#2a4d9c"/></svg>LEARN MORE</a>
</section>

<section class="banner banner--promo">
  <div class="photo photo--promo" role="img" aria-label="Smiling woman with curly hair in a denim jacket holding a phone"></div>
  <svg class="brackets" style="left:125px;top:92px" width="355" height="72" viewBox="0 0 355 72">
    <path d="M32 1H1V71H32"/><path d="M323 1H354V71H323"/>
  </svg>
  <h2 class="headline" style="left:302px;top:131px">CURRENT PROMOTIONS</h2>
  <a class="learn-more" style="left:252px;top:189px" href="#"><svg viewBox="0 0 23 6"><line x1="0" y1="3" x2="18" y2="3" stroke="#2a4d9c" stroke-width="1"/><path d="M17 0.5L22 3L17 5.5Z" fill="#2a4d9c"/></svg>LEARN MORE</a>
</section>

<section class="banner banner--clear">
  <div class="photo photo--clear" role="img" aria-label="Laughing woman with a platinum bob in a pink shirt"></div>
  <svg class="brackets" style="left:334px;top:70px" width="252" height="106" viewBox="0 0 252 106">
    <path d="M32 1H1V33"/><path d="M1 69V105H32"/><path d="M219 1H251V33"/><path d="M251 69V105H219"/>
  </svg>
  <h2 class="headline headline--stack" style="left:460px;top:120px">CLEARANCE<br>PRODUCTS</h2>
  <a class="learn-more" style="left:417px;top:200px" href="#"><svg viewBox="0 0 23 6"><line x1="0" y1="3" x2="18" y2="3" stroke="#2a4d9c" stroke-width="1"/><path d="M17 0.5L22 3L17 5.5Z" fill="#2a4d9c"/></svg>LEARN MORE</a>
</section>

</body>
</html>
```